A new presentation to our clients

we are a Real Estate agency, our website is www.lumibrasa.com and it’s time to have a new, fashion and remarcable Business Card. we want to differentiate ourselves from other companies so we want a business card that differentiates us. we want the business card to impact our customers. in the competitive market that we have today, we have to be different and it is this difference that we seek

Target Market(s)

Real Estate Clients

Contact Information for Business Card

We search a totaly diferent card from the usual

Font styles to use
Sans Serif

Colors
e34197

Requirements
Must have
• Logo, adress, phone contact, e-mail, photo, and our website
Nice to have
• We would like to see a modern business card
Should not have
• Houses or building draws

```html
<!DOCTYPE html>
<html lang="en">
<head>
<meta charset="UTF-8">
<title>Lumi Brasa — Business Card</title>
<link rel="stylesheet" href="https://fonts.googleapis.com/css2?family=Roboto:wght@400;500;700&display=swap">
<style>
  :root {
    --brand-pink: #e31c6e;
    --paper-white: #ffffff;
    --backdrop: #d3d3d3;
    --card-shadow: rgba(0, 0, 0, 0.18);
  }
  * { box-sizing: border-box; margin: 0; padding: 0; }
  html, body {
    width: 1200px; height: 800px; overflow: hidden;
    background: var(--backdrop);
    font-family: "Roboto", Arial, sans-serif;
  }
  .sheet {
    width: 1200px; height: 800px;
    display: flex; flex-direction: column;
    align-items: center; justify-content: center; gap: 44px;
  }
  .card {
    position: relative;
    width: 580px; height: 340px;
    background: var(--brand-pink);
    box-shadow: 0 6px 16px var(--card-shadow);
    overflow: hidden;
  }
  .card-front {
    display: flex; align-items: center; justify-content: center;
  }
  .brand-name {
    font-weight: 700;
    letter-spacing: 1px;
    white-space: nowrap;
  }
  .card-front .brand-name {
    color: var(--paper-white);
    font-size: 62px;
  }
  .brand-strip {
    position: absolute; left: 0; top: 0; bottom: 0;
    width: 140px;
    background: var(--paper-white);
  }
  .brand-strip::after {
    content: "";
    position: absolute; top: 0; bottom: 0; right: 7px;
    width: 3px; background: var(--brand-pink);
  }
  .brand-strip .brand-name {
    position: absolute; left: 62px; top: 50%;
    transform: translate(-50%, -50%) rotate(-90deg);
    color: var(--brand-pink);
    font-size: 50px;
  }
  .contact-block {
    position: absolute; right: 30px; top: 28px;
    color: var(--paper-white);
    text-align: right;
  }
  .person-name {
    font-size: 19px; font-weight: 500; letter-spacing: 0.5px;
    text-transform: uppercase;
  }
  .person-role {
    font-size: 12px; margin-top: 2px;
  }
  .contact-list {
    list-style: none; margin-top: 24px;
    font-size: 12.5px; line-height: 19px;
  }
  .contact-list li {
    display: flex; justify-content: flex-end; align-items: center; gap: 7px;
  }
  .contact-list svg { width: 11px; height: 11px; fill: none; stroke: var(--paper-white); stroke-width: 1.6; }
  .address {
    margin-top: 26px; font-size: 12.5px; line-height: 19px;
    padding-right: 18px;
  }
</style>
</head>
<body>
<main class="sheet">
  <section class="card card-front" aria-label="Business card front">
    <span class="brand-name">Lumi Brasa</span>
  </section>

  <section class="card card-back" aria-label="Business card back">
    <div class="brand-strip">
      <span class="brand-name">Lumi Brasa</span>
    </div>
    <div class="contact-block">
      <p class="person-name">Daniel Moreira</p>
      <p class="person-role">Director</p>
      <ul class="contact-list">
        <li>(+351) 220 418 530
          <svg viewBox="0 0 12 12" aria-hidden="true"><path d="M3 1.5 L4.5 4 L3.5 5 Q5 7.5 7 8.5 L8 7.5 L10.5 9 L9.5 10.5 Q5 10.5 1.5 3 Z"/></svg>
        </li>
        <li>(+351) 220 418 539
          <svg viewBox="0 0 12 12" aria-hidden="true"><rect x="3.5" y="1" width="5" height="10" rx="1"/><line x1="5.5" y1="9.3" x2="6.5" y2="9.3"/></svg>
        </li>
        <li>geral@lumibrasa.com
          <svg viewBox="0 0 12 12" aria-hidden="true"><rect x="1" y="2.5" width="10" height="7"/><path d="M1 2.5 L6 6.5 L11 2.5"/></svg>
        </li>
        <li>www.lumibrasa.com
          <svg viewBox="0 0 12 12" aria-hidden="true"><circle cx="6" cy="6" r="4.8"/><ellipse cx="6" cy="6" rx="2" ry="4.8"/><line x1="1.2" y1="6" x2="10.8" y2="6"/></svg>
        </li>
      </ul>
      <address class="address" style="font-style:normal">
        Rua das Camélias, 148<br>
        4150-206, Porto
      </address>
    </div>
  </section>
</main>
</body>
</html>
```